Local fast-growing company in the service sector

We are looking for a modern business card design, which should also appear on our letterheads

Target Market(s)

Private and industrial sectors

Contact Information for Business Card

Vorname Name
Kellberger Str. 18
72468 Auenbach
Tel.: 07146-839214-0
Name@agentur-kvtl.de

Colors
9d9d9d
919191
aaaaaa

Requirements
Must have
• The logo (file) in silver

```html
<!DOCTYPE html>
<html lang="de">
<head>
<meta charset="utf-8">
<title>KVTL – Visitenkarte</title>
<link rel="stylesheet" href="https://fonts.googleapis.com/css2?family=Roboto:wght@400;700&family=Roboto+Condensed:wght@400&display=swap">
<style>
  :root {
    --stage: #2a2a2a;
    --card-front: #f4f4f4;
    --text-dark: #555555;
    --text-name: #7a7a7a;
    --silver: #9d9d9d;
    --silver-mid: #919191;
    --silver-light: #aaaaaa;
    --divider: #c8c8c8;
    --white: #ffffff;
  }
  * { margin: 0; padding: 0; box-sizing: border-box; }
  html, body { width: 1200px; height: 960px; overflow: hidden; background: var(--stage); }
  .stage { position: relative; width: 1200px; height: 960px; font-family: "Roboto", Arial, sans-serif; }

  .card { position: absolute; width: 600px; height: 343px; box-shadow: 0 3px 8px rgba(0,0,0,.5); overflow: hidden; }
  .card--front { left: 314px; top: 113px; background: var(--card-front); }
  .card--back {
    left: 311px; top: 472px;
    background: radial-gradient(ellipse 60% 80% at 50% 35%, #c4c4c4 0%, var(--silver-mid) 55%, #727272 100%);
  }

  .edge-tab { position: absolute; top: 99px; width: 16px; height: 144px;
    background: linear-gradient(90deg, #6f6f6f, #d6d6d6 50%, #8a8a8a); }
  .edge-tab--left { left: 0; border-radius: 0 6px 6px 0; }
  .edge-tab--right { right: 0; border-radius: 6px 0 0 6px; }

  .brand { position: absolute; display: flex; align-items: center; gap: 10px; }
  .brand__mark { background: var(--silver); }
  .brand__name { font-weight: 700; letter-spacing: 1px; line-height: 1; }

  .card--front .brand { left: 74px; top: 142px; }
  .card--front .brand__mark { width: 30px; height: 30px; }
  .card--front .brand__name { font-size: 44px; color: var(--silver); }

  .divider { position: absolute; left: 313px; top: 100px; width: 1px; height: 147px; background: var(--divider); }

  .contact { position: absolute; left: 339px; top: 101px; color: var(--text-dark); font-size: 14.5px; line-height: 18px; }
  .contact__name { font-family: "Roboto Condensed", "Arial Narrow", sans-serif; font-size: 23px; color: var(--text-name); line-height: 28px; margin-bottom: 8px; }
  .contact__address { margin-bottom: 10px; }
  .contact__row { display: flex; align-items: center; gap: 8px; height: 19px; }
  .contact__row svg { width: 14px; height: 14px; flex: none; fill: var(--text-name); }

  .card--back .brand { left: 50%; top: 118px; transform: translateX(-50%); gap: 14px; }
  .card--back .brand__mark { width: 40px; height: 40px; background: #d8d8d8; }
  .card--back .brand__name { font-size: 62px; color: var(--white); }

  .back__url { position: absolute; left: 0; right: 0; top: 286px; text-align: center; color: var(--white); font-size: 15px; letter-spacing: 6px; }
</style>
</head>
<body>
<main class="stage">
  <section class="card card--front">
    <span class="edge-tab edge-tab--left"></span>
    <span class="edge-tab edge-tab--right"></span>

    <div class="brand">
      <span class="brand__mark"></span>
      <span class="brand__name">KVTL</span>
    </div>

    <span class="divider"></span>

    <div class="contact">
      <p class="contact__name">LENA BRANDT</p>
      <p class="contact__address">Kellberger Str. 18<br>72468 Auenbach</p>
      <p class="contact__row">
        <svg viewBox="0 0 24 24"><path d="M6.6 10.8a15.1 15.1 0 0 0 6.6 6.6l2.2-2.2c.3-.3.7-.4 1-.2 1.1.4 2.3.6 3.6.6.6 0 1 .4 1 1V20c0 .6-.4 1-1 1A17 17 0 0 1 3 4c0-.6.4-1 1-1h3.5c.6 0 1 .4 1 1 0 1.3.2 2.5.6 3.6.1.3 0 .7-.2 1z"/></svg>
        07146-839214-0
      </p>
      <p class="contact__row">
        <svg viewBox="0 0 24 24"><path d="M3 5h18v14H3z M4 6.5v1l8 5 8-5v-1z" fill-rule="evenodd"/></svg>
        Name@agentur-kvtl.de
      </p>
      <p class="contact__row">
        <svg viewBox="0 0 24 24"><circle cx="12" cy="12" r="10"/></svg>
        www.agentur-kvtl.de
      </p>
    </div>
  </section>

  <section class="card card--back">
    <div class="brand">
      <span class="brand__mark"></span>
      <span class="brand__name">KVTL</span>
    </div>
    <p class="back__url">www.agentur-kvtl.de</p>
  </section>
</main>
</body>
</html>
```